Gestaltung Mini Katalog für bayerische Polomarke
Gestaltung "Mini" Katalog für bayerische Polomarke
Zielgruppe
Unsere Marke richtet sich an den klassischen Lifestyle Kunden. 20 - 45 Jahre alt, legt Wert auf das Äussere und Kleidung.... Mag es gerne besonders, modern und chic.
Hallo,
wir planen derzeit einen kleinen Katalog von 8-10 Seiten im Format DIN A5 (kein Muss). Präsentiert wird darin die erste bayerische Polomarke K&M reitmode und die aktuellen Kollektionen an Polo-Teamshirts.
Die Fotos dazu werden in den nächsten 14 Tagen entstehen.
Wir suchen nun jemanden, der uns das ganze in eine moderne Gestaltung bringt. Für Vorschläge bitte statt der Fotos alternative Fotos einsetzen.
Unsere Marke bewegt sich im mittleren Preissegment und präsentiert eine ganz besondere Sportart. All das muss in dem Katalog rüber kommen. Neben den Produkt- und Modefotos werden klassische Polobilder integriert, um das Gefühl diesen Sports mit zu vermitteln.
Die Grundfarben sollten sich an denen von K&M reitmode orientieren: schwarz, blau, weiss.... Wobei wir für andere Farben, wenn diese passen bzw. begründet sind auch interessiert sind.

```html
<!DOCTYPE html>
<html lang="de">
<head>
<meta charset="utf-8">
<title>K&amp;M Shirts für Männer</title>
<link rel="stylesheet" href="https://fonts.googleapis.com/css2?family=Crimson+Pro:wght@500;700&display=swap">
<style>
  :root {
    --bg: #231f20;
    --cyan: #1fb6cc;
    --white: #ffffff;
    --top-strip: #f2f2f2;
    --shirt-slate: #4a5566;
    --shirt-white: #f4f4f4;
    --shirt-black: #141414;
  }
  * { margin: 0; padding: 0; box-sizing: border-box; }
  html, body { width: 1200px; height: 1200px; overflow: hidden; background: var(--bg); }
  .page {
    position: relative;
    width: 1200px; height: 1200px;
    background: var(--bg);
    font-family: "Crimson Pro", "Times New Roman", serif;
    color: var(--white);
  }
  .top-strip { position: absolute; left: 0; top: 0; width: 1200px; height: 52px; background: var(--top-strip); }
  .title-band {
    position: absolute; left: 0; top: 52px; width: 1200px; height: 95px;
    background: var(--cyan);
  }
  .page-title {
    position: absolute; right: 18px; top: 66px;
    font-size: 52px; font-weight: 700; color: var(--white); line-height: 1;
  }
  .product { position: absolute; width: 420px; text-align: center; }
  .product-frame {
    position: absolute;
    border: 6px solid var(--cyan);
    background: var(--white);
    padding: 26px;
  }
  .product-photo { width: 100%; height: 100%; border-radius: 4px; }
  .photo-slate { background: radial-gradient(ellipse at center, var(--shirt-slate) 55%, #dfe3e8 100%); }
  .photo-white { background: radial-gradient(ellipse at center, var(--shirt-white) 55%, #d9d9d9 100%); }
  .photo-black { background: radial-gradient(ellipse at center, var(--shirt-black) 55%, #cfcfcf 100%); }
  .product-name { font-size: 27px; font-weight: 700; line-height: 1.1; }
  .product-number { font-size: 23px; font-weight: 500; color: var(--cyan); line-height: 1.3; }
  .product-sizes { font-size: 23px; font-weight: 700; line-height: 1.3; }
  .product-price { font-size: 56px; font-weight: 700; color: var(--cyan); line-height: 1.05; }
  .brand-mark {
    position: absolute; left: 500px; top: 585px; width: 200px;
    text-align: center;
    font-size: 40px; font-weight: 500; color: var(--white); line-height: 1.05;
  }
</style>
</head>
<body>
<main class="page">
  <div class="top-strip"></div>
  <div class="title-band"></div>
  <h1 class="page-title">K&amp;M Shirts für Männer</h1>

  <div class="product-frame" style="left:137px; top:161px; width:325px; height:343px;">
    <div class="product-photo photo-slate" role="img" aria-label="Graublaues Herren-T-Shirt mit blauem Polospieler-Motiv"></div>
  </div>
  <div class="product" style="left:89px; top:522px;">
    <p class="product-name">Shirt für Männer</p>
    <p class="product-number">Best.-Nr.: 080101</p>
    <p class="product-sizes">Größen: S - M - L - XL - XXL</p>
    <p class="product-price">25,00 €</p>
  </div>

  <div class="product-frame" style="left:734px; top:161px; width:325px; height:343px;">
    <div class="product-photo photo-white" role="img" aria-label="Weißes Herren-T-Shirt mit schwarzem Polospieler-Motiv"></div>
  </div>
  <div class="product" style="left:686px; top:522px;">
    <p class="product-name">Shirt für Männer</p>
    <p class="product-number">Best.-Nr.: 080101c</p>
    <p class="product-sizes">Größen: S - M - L - XL - XXL</p>
    <p class="product-price">25,00 €</p>
  </div>

  <div class="brand-mark">K&amp;M<br>reitmode</div>

  <div class="product-frame" style="left:137px; top:691px; width:325px; height:327px;">
    <div class="product-photo photo-black" role="img" aria-label="Schwarzes Herren-Poloshirt mit kleinem Brustmotiv"></div>
  </div>
  <div class="product" style="left:89px; top:1028px;">
    <p class="product-name">Poloshirt für Männer</p>
    <p class="product-number">Best.-Nr.: 080102</p>
    <p class="product-sizes">Größen: S - M - L - XL - XXL</p>
    <p class="product-price">49,95 €</p>
  </div>

  <div class="product-frame" style="left:753px; top:691px; width:325px; height:327px;">
    <div class="product-photo photo-black" role="img" aria-label="Schwarzes langärmeliges Herrenpolohemd mit Nummer und blauem Aufdruck"></div>
  </div>
  <div class="product" style="left:705px; top:1028px;">
    <p class="product-name">Herrenpolohemd</p>
    <p class="product-number">Best.-Nr.: 080809</p>
    <p class="product-sizes">Größen: S - M - L - XL - XXL</p>
    <p class="product-price">119,95 €</p>
  </div>
</main>
</body>
</html>
```